4th Generation Family Business Needs a New Card Design!

We are a family owned 4th Generation company. We are based in the Sydney, Australia area and we are desperately in need of a more modern and classy card. We are monumental masons who design, supply & erect lasting memorials throughout cemeteries in Sydney. Our customers are normally in a period of grieving. I have attached logo files that will need to be implemented on the card. Company was established 1935. Australian Owned and Operated. Card needs to be designed to PIXO.com specification.

Target Market(s)

Our target market is based upon people that a grieving for family members that have passed away. We also deal with alot of companies that own and operate cemeteries.

Industry/Entity Type

Business

Contact Information for Business Card

Simon Harcourt, Operations Manager, 0417293086, simon@harcourtmemorials.com.au
Lewis Harcourt, Director, 0491630572, lewis@harcourtmemorials.com.au
Phone # 02 9561 3048
Website: www.harcourtmemorials.com.au
Address: Suite 17, 8 Palfrey Lane, West Carlow, Sydney NSW 2156

Font styles to use
Serif
Decorative
Script

Requirements
Must have
• Would like to see the logo nicely implemented with a modern design. Embossed lettering would be a nice additive.

```html
<!DOCTYPE html>
<html lang="en">
<head>
<meta charset="utf-8">
<title>Harcourt Memorials – Business Card</title>
<link rel="stylesheet" href="https://fonts.googleapis.com/css2?family=Cinzel:wght@400;600&family=Roboto:wght@300;400&display=swap">
<style>
  :root {
    --backdrop: #3a302b;
    --card: #1d1d1e;
    --card-edge: #2a2a2b;
    --gold: #f2c230;
    --gold-text: #e8b92a;
    --white: #ffffff;
    --text-soft: #c9c9c9;
    --rule: #3a3a3a;
  }
  * { margin: 0; padding: 0; box-sizing: border-box; }
  html, body { width: 1200px; height: 716px; overflow: hidden; }
  body {
    background: var(--backdrop);
    font-family: "Roboto", Arial, sans-serif;
    position: relative;
  }
  .card {
    position: absolute;
    top: 203px;
    width: 540px;
    height: 310px;
    background: var(--card);
    border: 1px solid var(--card-edge);
    overflow: hidden;
  }
  .card--back { left: 40px; }
  .card--front { left: 620px; }

  /* Back card */
  .brand-mark {
    position: absolute;
    top: 34px;
    right: 36px;
    display: flex;
    align-items: center;
    gap: 8px;
    font-family: "Cinzel", Georgia, serif;
    font-weight: 400;
    font-size: 15px;
    color: var(--white);
    letter-spacing: 1px;
  }
  .brand-mark__square {
    width: 12px; height: 12px;
    background: var(--white);
  }
  .divider {
    position: absolute;
    top: 92px; left: 0; right: 0;
    height: 1px;
    background: var(--rule);
  }
  .person {
    position: absolute;
    left: 36px;
    top: 118px;
  }
  .person__name {
    font-family: "Cinzel", Georgia, serif;
    font-weight: 600;
    font-size: 19px;
    color: var(--gold-text);
    letter-spacing: 0.5px;
  }
  .person__title {
    font-size: 11px;
    color: var(--text-soft);
    margin-top: 3px;
  }
  .contacts {
    position: absolute;
    left: 36px;
    top: 180px;
    list-style: none;
  }
  .contacts li {
    display: flex;
    align-items: center;
    gap: 8px;
    font-size: 12px;
    font-weight: 300;
    color: var(--text-soft);
    line-height: 17px;
  }
  .contacts svg { width: 9px; height: 9px; fill: var(--gold); flex: none; }
  .address {
    position: absolute;
    right: 36px;
    top: 118px;
    text-align: right;
    font-size: 11px;
    font-weight: 300;
    color: var(--text-soft);
    line-height: 16px;
  }
  .bands {
    position: absolute;
    left: 0; bottom: 0;
    width: 540px; height: 110px;
  }

  /* Front card */
  .wordmark {
    position: absolute;
    inset: 0;
    display: flex;
    align-items: center;
    justify-content: center;
    gap: 14px;
    font-family: "Cinzel", Georgia, serif;
    font-weight: 400;
    font-size: 36px;
    color: var(--white);
    letter-spacing: 2px;
  }
  .wordmark__circle {
    width: 14px; height: 14px;
    border-radius: 50%;
    background: var(--white);
  }
</style>
</head>
<body>

<section class="card card--back" aria-label="Business card contact side">
  <div class="brand-mark">
    <span class="brand-mark__square"></span>
    <span>Harcourt Memorials</span>
  </div>
  <div class="divider"></div>

  <div class="person">
    <div class="person__name">Simon Harcourt</div>
    <div class="person__title">Operations Manager</div>
  </div>

  <ul class="contacts">
    <li><svg viewBox="0 0 10 10"><rect x="2.5" y="0" width="5" height="10" rx="1"/></svg>0417293086</li>
    <li><svg viewBox="0 0 10 10"><path d="M2 0h2l1 3-1.5 1a6 6 0 0 0 2.5 2.5L7 5l3 1v2a2 2 0 0 1-2 2A8 8 0 0 1 0 2a2 2 0 0 1 2-2z"/></svg>02 9561 3048</li>
    <li><svg viewBox="0 0 10 10"><path d="M0 2h10v6H0z M0 2l5 3 5-3" /></svg>simon@harcourtmemorials.com.au</li>
    <li><svg viewBox="0 0 10 10"><circle cx="5" cy="5" r="5"/></svg>www.harcourtmemorials.com.au</li>
  </ul>

  <div class="address">
    Suite 17, 8 Palfrey Lane,<br>
    West Carlow, Sydney NSW 2156
  </div>

  <svg class="bands" viewBox="0 0 540 110" aria-hidden="true">
    <polygon points="390,66 540,66 540,110 370,110" fill="var(--gold)"/>
    <polygon points="0,92 360,80 352,110 0,110" fill="var(--white)"/>
  </svg>
</section>

<section class="card card--front" aria-label="Business card brand side">
  <div class="wordmark">
    <span class="wordmark__circle"></span>
    <span>Harcourt Memorials</span>
  </div>
</section>

</body>
</html>
```